business card deign

Logo needs the following on it.
1. attached logo
2. Tagline - "Cold drinks, good tunes and long summer nights...all on us!"
3. Name- Dalton Pikes, Founder and CPO
4. Address - 412 E. Carver Avenue, Ste 2207, Tampa, FL. 33917
5. Phone - 555.318.4726

```html
<!DOCTYPE html>
<html lang="en">
<head>
<meta charset="utf-8">
<title>Frostly Business Card</title>
<link rel="stylesheet" href="https://fonts.googleapis.com/css2?family=Montserrat:wght@400;500;700&display=swap">
<style>
  :root {
    --bg: #3a3a3c;
    --card-light: #ffffff;
    --card-dark: #262627;
    --ink: #111111;
    --ink-soft: #2b2b2b;
    --emboss: #8c8c8c;
  }
  * { margin: 0; padding: 0; box-sizing: border-box; }
  html, body { width: 1200px; height: 1200px; overflow: hidden; }
  body {
    background: var(--bg);
    font-family: "Montserrat", sans-serif;
    position: relative;
  }
  .card {
    position: absolute;
    width: 760px;
    height: 434px;
    border-radius: 34px;
    overflow: hidden;
  }
  .card--front { left: 90px; top: 90px; background: var(--card-light); color: var(--ink); }
  .card--back { left: 350px; top: 660px; background: var(--card-dark); }

  .contact { position: absolute; left: 56px; top: 150px; }
  .contact__name { font-size: 34px; font-weight: 700; letter-spacing: 0.5px; line-height: 1; }
  .contact__title { font-size: 19px; font-weight: 400; letter-spacing: 1px; margin-top: 4px; color: var(--ink-soft); }
  .contact__row { display: flex; align-items: flex-start; gap: 12px; margin-top: 14px; font-size: 21px; line-height: 1.2; color: var(--ink-soft); }
  .contact__row svg { flex: none; width: 22px; height: 22px; margin-top: 2px; }

  .brand { position: absolute; display: flex; align-items: center; gap: 14px; }
  .card--front .brand { right: 60px; top: 150px; }
  .brand__dot { width: 22px; height: 22px; border-radius: 50%; background: var(--ink); }
  .brand__name { font-size: 44px; font-weight: 700; letter-spacing: 10px; }
  .card--back .brand { left: 50%; top: 50%; transform: translate(-50%, -50%); }
  .card--back .brand__dot { width: 32px; height: 32px; background: var(--emboss); }
  .card--back .brand__name { font-size: 64px; letter-spacing: 14px; color: var(--emboss); }

  .tagline {
    position: absolute; left: 0; right: 0; bottom: 52px;
    text-align: center; font-size: 21px; font-weight: 700; color: var(--ink);
  }
</style>
</head>
<body>
  <section class="card card--front">
    <div class="contact">
      <p class="contact__name">DALTON PIKES</p>
      <p class="contact__title">FOUNDER AND CPO</p>
      <div class="contact__row">
        <svg viewBox="0 0 24 24" aria-hidden="true"><path fill="#111" d="M6.6 10.8a15.2 15.2 0 0 0 6.6 6.6l2.2-2.2a1 1 0 0 1 1-.25 11.4 11.4 0 0 0 3.6.57 1 1 0 0 1 1 1V20a1 1 0 0 1-1 1A17 17 0 0 1 3 4a1 1 0 0 1 1-1h3.5a1 1 0 0 1 1 1c0 1.250.2 2.450.57 3.570a1 1 0 0 1-.25 1z"/></svg>
        <span>555.318.4726</span>
      </div>
      <div class="contact__row">
        <svg viewBox="0 0 24 24" aria-hidden="true"><path fill="none" stroke="#111" stroke-width="2.2" d="M12 22s-7-7.2-7-12a7 7 0 0 1 14 0c0 4.8-7 12-7 12z"/><circle cx="12" cy="10" r="2.6" fill="none" stroke="#111" stroke-width="2.2"/></svg>
        <span>412 E. Carver Avenue,<br>Ste 2207, Tampa, FL. 33917</span>
      </div>
    </div>
    <div class="brand">
      <span class="brand__dot"></span>
      <span class="brand__name">FROSTLY</span>
    </div>
    <p class="tagline">Cold drinks, good tunes and long summer nights...all on us!</p>
  </section>

  <section class="card card--back">
    <div class="brand">
      <span class="brand__dot"></span>
      <span class="brand__name">FROSTLY</span>
    </div>
  </section>
</body>
</html>
```